Ward Compass Business Card Design*

We need a business card design for our company Ward Compass. Our company is specialized in providing online consulting services regarding medical institutions, hospitals and doctors. We work with patients worldwide looking to choose between healthcare providers. We have a website you may use as a reference, where we list doctors and clinics worldwide. So we target Medical providers as well as patients worldwide.
Target Market(s)
Medical Providers and patients around the world
Industry/Entity Type
Medical
Contact Information for Business Card
Salwa Kettani
CEO
+90 612 348 2175
info@wardcompass.example
www.wardcompass.example
14 Annakhil 7 H.R.B. Rabat, Morocco
Requirements
Must have
- Company logo/name on one full side, personal info and smaller logo and company name on the other side.
Nice to have
- Smart and elegant design

```html
<!DOCTYPE html>
<html lang="en">
<head>
<meta charset="utf-8">
<title>Ward Compass — Business Card</title>
<link href="https://fonts.googleapis.com/css2?family=Montserrat:wght@300;400;700&family=Open+Sans:wght@400&display=swap" rel="stylesheet">
<style>
  :root {
    --backdrop: #1d1d1f;
    --brand-blue: #2776b8;
    --deep-blue: #1f4f7f;
    --slate: #7f7f7f;
    --ink: #3a3a3a;
    --paper: #ffffff;
    --card-w: 330px;
    --card-h: 578px;
  }
  * { box-sizing: border-box; margin: 0; padding: 0; }
  html, body { width: 1200px; height: 823px; overflow: hidden; }
  body {
    background: var(--backdrop);
    display: flex;
    align-items: center;
    justify-content: center;
    gap: 70px;
    font-family: "Montserrat", sans-serif;
  }
  .card {
    position: relative;
    width: var(--card-w);
    height: var(--card-h);
    overflow: hidden;
    box-shadow: 0 12px 30px rgba(0,0,0,.55);
  }

  /* Front */
  .card-front {
    background: var(--brand-blue);
    display: flex;
    flex-direction: column;
    align-items: center;
    justify-content: flex-end;
    padding-bottom: 70px;
  }
  .brand-ring {
    width: 92px;
    height: 92px;
    border: 14px solid var(--paper);
    border-radius: 50%;
    margin-bottom: 30px;
  }
  .brand-name {
    color: var(--paper);
    font-weight: 400;
    font-size: 26px;
    letter-spacing: 1px;
    text-transform: uppercase;
  }

  /* Back */
  .card-back { background: var(--paper); }
  .card-back .backdrop-shapes { position: absolute; inset: 0; width: 100%; height: 100%; }
  .holder {
    position: absolute;
    top: 48px;
    right: 34px;
    text-align: right;
  }
  .holder-name {
    font-size: 27px;
    letter-spacing: .5px;
    text-transform: uppercase;
    color: var(--ink);
    font-weight: 300;
    white-space: nowrap;
  }
  .holder-name strong { color: var(--brand-blue); font-weight: 700; }
  .holder-role {
    display: inline-block;
    margin-top: 4px;
    padding-bottom: 6px;
    border-bottom: 1.5px solid var(--ink);
    font-size: 12px;
    font-weight: 700;
    letter-spacing: 1px;
    color: var(--ink);
    width: 58px;
    text-align: left;
  }
  .back-brand {
    position: absolute;
    top: 205px;
    left: 0;
    right: 0;
    display: flex;
    flex-direction: column;
    align-items: center;
  }
  .back-brand .brand-ring {
    width: 78px;
    height: 78px;
    border: 12px solid var(--deep-blue);
    margin-bottom: 14px;
  }
  .back-brand .brand-name {
    color: var(--slate);
    font-size: 17px;
  }
  .contacts {
    position: absolute;
    left: 26px;
    bottom: 40px;
    list-style: none;
    font-family: "Open Sans", sans-serif;
    font-size: 13px;
    color: var(--paper);
  }
  .contacts li {
    display: flex;
    align-items: center;
    gap: 10px;
    margin-top: 10px;
  }
  .contact-icon {
    width: 24px;
    height: 24px;
    border-radius: 50%;
    background: var(--brand-blue);
    display: flex;
    align-items: center;
    justify-content: center;
    flex-shrink: 0;
  }
  .contact-icon svg { width: 13px; height: 13px; }
</style>
</head>
<body>

  <section class="card card-front" aria-label="Card front">
    <div class="brand-ring"></div>
    <div class="brand-name">Ward Compass</div>
  </section>

  <section class="card card-back" aria-label="Card back">
    <svg class="backdrop-shapes" viewBox="0 0 330 578" preserveAspectRatio="none" aria-hidden="true">
      <rect width="330" height="578" fill="var(--slate)"/>
      <path d="M0 330 Q90 470 330 520 V495 Q110 455 0 300 Z" fill="var(--brand-blue)"/>
      <path d="M0 0 H330 V495 Q110 455 0 300 Z" fill="var(--paper)"/>
    </svg>

    <div class="holder">
      <div class="holder-name"><strong>Salwa</strong> Kettani</div>
      <div class="holder-role">CEO</div>
    </div>

    <div class="back-brand">
      <div class="brand-ring"></div>
      <div class="brand-name">Ward Compass</div>
    </div>

    <ul class="contacts">
      <li>
        <span class="contact-icon">
          <svg viewBox="0 0 24 24"><path fill="#fff" d="M6.6 10.8a15.1 15.1 0 0 0 6.6 6.6l2.2-2.2c.3-.3.7-.4 1-.2 1.1.4 2.3.6 3.6.6.6 0 1 .4 1 1V20c0 .6-.4 1-1 1A17 17 0 0 1 3 4c0-.6.4-1 1-1h3.5c.6 0 1 .4 1 1 0 1.3.2 2.5.6 3.6.1.3 0 .7-.2 1z"/></svg>
        </span>
        +90 612 348 2175
      </li>
      <li>
        <span class="contact-icon">
          <svg viewBox="0 0 24 24"><path fill="#fff" d="M3 5h18v14H3z"/><path fill="none" stroke="#2776b8" stroke-width="2" d="M3 5l9 8 9-8"/></svg>
        </span>
        info@wardcompass.example
      </li>
      <li>
        <span class="contact-icon">
          <svg viewBox="0 0 24 24"><circle cx="12" cy="12" r="9" fill="none" stroke="#fff" stroke-width="2"/><path fill="none" stroke="#fff" stroke-width="1.6" d="M3 12h18M12 3c3 3 3 15 0 18M12 3c-3 3-3 15 0 18"/></svg>
        </span>
        www.wardcompass.example
      </li>
    </ul>
  </section>

</body>
</html>
```